Desktop and Networking Support Course 9.17.25

Important the ad should not be very busy with the text taking up the major part of the ad .. please do not make the text so big that it takes up most of the ad..
Flyer Design Brief for Graphic Artist
also i am looking for something unique or creative that it will stand out .
Size & Layout:
Full Page with Bleed: 8” x 10.75” + 0.25” bleed on all sides.
Footer Space: Leave a 1-inch margin at the bottom for footer content (e.g., contact info, logo, or call-to-action).
Target Audience:
College-age students (around 24 years old)
Located in the USA
Interested in creative, professional, and career-building opportunities
Purpose:
To attract students to enroll in a college program
Flyer should be eye-catching, unique, and creative
Text must be clear and readable,
Design Style:
Use vector art, typography, or photography — your choice
If using photography, feature a white young professional USA citizen:
Wearing a white collared shirt
not with long hair
Creative Direction:
The flyer should stand out visually — something people would want to look at and keep
Showcase creativity and professionalism
Use bold colors, dynamic layout, or unexpected design elements to grab attention
Avoid clutter — keep the design balanced and clean
Text Suggestions (can be adjusted):
Footer,
please leave one inch on the bottom for the footer

```html
<!DOCTYPE html>
<html lang="en">
<head>
<meta charset="utf-8">
<title>Desktop &amp; Network Support Course Flyer</title>
<link href="https://fonts.googleapis.com/css2?family=Anton&family=Unbounded:wght@700;800&family=Poppins:wght@500;600;700;800&display=swap" rel="stylesheet">
<style>
  :root{
    --green-deep:#0e2a0c;
    --green-bright:#0f9a12;
    --lime:#8df20f;
    --lime-glow:#efffb0;
    --white:#ffffff;
    --ink:#111111;
    --rule:rgba(255,255,255,.7);
  }
  *{margin:0;padding:0;box-sizing:border-box}
  html,body{width:901px;height:1200px;overflow:hidden;background:var(--white)}
  .flyer{position:relative;width:901px;height:1200px;background:var(--white);font-family:"Poppins",sans-serif;color:var(--white)}
  .hero{position:absolute;left:0;top:0;width:901px;height:1033px;overflow:hidden;
    background:
      radial-gradient(ellipse 340px 300px at 900px 0px,var(--lime-glow) 0%,#b9ec4e 25%,rgba(120,200,40,.6) 50%,rgba(60,150,30,0) 100%),
      radial-gradient(ellipse 520px 700px at 760px 420px,#4fa82a 0%,rgba(40,120,25,.7) 45%,rgba(20,70,15,0) 100%),
      linear-gradient(160deg,#17461a 0%,#1c5417 40%,#173f12 70%,var(--green-deep) 100%);}
  .footer{position:absolute;left:0;top:1033px;width:901px;height:167px;background:var(--white)}
  .photo{position:absolute;left:590px;top:143px;width:240px;height:817px;
    border-radius:120px 120px 40px 40px;
    background:linear-gradient(180deg,rgba(255,255,255,.55) 0%,rgba(245,245,245,.45) 45%,rgba(130,130,130,.55) 60%,rgba(110,110,110,.5) 95%)}
  .headline-your{position:absolute;left:120px;top:54px;font-family:"Unbounded",sans-serif;font-weight:800;font-size:52px;letter-spacing:-1.5px;color:var(--white);transform:rotate(-3deg);transform-origin:left bottom}
  .headline-career{position:absolute;left:116px;top:104px;transform:rotate(-3deg);transform-origin:0 140px;overflow:visible}
  .headline-just{position:absolute;left:119px;top:246px;font-family:"Unbounded",sans-serif;font-weight:800;font-size:47px;letter-spacing:-1.8px;line-height:1;white-space:nowrap;transform:rotate(-3deg);transform-origin:left bottom}
  .click-pill{position:absolute;left:118px;top:297px;width:244px;height:50px;background:var(--white);border-radius:28px;
    transform:rotate(-5deg);display:flex;align-items:center;gap:10px;padding-left:22px;color:var(--ink);
    font-weight:700;font-size:26px;white-space:nowrap;box-shadow:0 6px 12px rgba(0,0,0,.25)}
  .course-name{position:absolute;left:386px;top:240px;font-weight:700;font-size:23px;line-height:1.28;white-space:nowrap;transform:rotate(-4deg);transform-origin:left top}
  .course-name .accent{color:var(--lime)}
  .tagline{position:absolute;left:116px;top:398px;font-weight:700;font-size:25px;white-space:nowrap;transform:rotate(-3.5deg);transform-origin:left top}
  .tagline .accent{color:var(--lime)}
  .stat-pill{position:absolute;left:115px;width:452px;height:74px;border-radius:38px;background:var(--green-bright);
    transform:rotate(-3deg);transform-origin:left top;display:flex;align-items:center;box-shadow:0 6px 12px rgba(0,0,0,.3)}
  .stat-pill.one{top:446px}
  .stat-pill.two{top:532px}
  .stat-badge{width:172px;height:74px;border-radius:38px;background:var(--white);color:var(--ink);display:flex;flex-direction:column;justify-content:center;padding-left:30px}
  .stat-badge .big{font-family:"Unbounded",sans-serif;font-weight:800;font-size:37px;line-height:1}
  .stat-badge .small{font-weight:700;font-size:12px}
  .stat-badge .lead{font-weight:700;font-size:11px;line-height:1}
  .stat-badge .mid{font-family:"Unbounded",sans-serif;font-weight:800;font-size:23px;line-height:1.05;white-space:nowrap}
  .stat-label{font-family:"Unbounded",sans-serif;font-weight:800;font-size:19px;padding-left:16px;white-space:nowrap}
  .source{position:absolute;left:115px;top:626px;font-weight:800;font-size:26px;white-space:nowrap;transform:rotate(-3.5deg);transform-origin:left top}
  .source .accent{color:var(--lime)}
  .checklist{position:absolute;left:115px;top:688px;width:396px;list-style:none;transform:rotate(-3deg);transform-origin:left top}
  .checklist li{display:flex;align-items:center;gap:10px;height:53px;font-weight:600;font-size:18px;white-space:nowrap}
  .checklist li+li{border-top:1px solid var(--rule)}
  .checklist svg{flex:none}
  .option-pill{position:absolute;left:115px;width:466px;height:50px;border:1.5px solid var(--green-bright);border-radius:28px;
    background:rgba(10,40,10,.35);transform:rotate(-3deg);transform-origin:left top;display:flex;align-items:center;padding-left:20px;
    font-weight:700;font-size:19px;letter-spacing:3.4px;white-space:nowrap}
  .option-pill.one{top:866px}
  .option-pill.two{top:924px}
</style>
</head>
<body>
<div class="flyer">
  <section class="hero">
    <div class="photo" role="img" aria-label="Photo of a smiling young professional in a white collared shirt and grey trousers, pointing up over his shoulder"></div>

    <div class="headline-your">Your</div>
    <svg class="headline-career" width="400" height="150" viewBox="0 0 400 150" aria-label="CAREER">
      <text x="0" y="140" fill="var(--lime)" font-family="Anton, sans-serif" font-size="164" textLength="390" lengthAdjust="spacingAndGlyphs">CAREER</text>
    </svg>
    <div class="headline-just">Is Just a</div>
    <div class="click-pill">
      <svg width="22" height="30" viewBox="0 0 22 30" fill="none" stroke="var(--ink)" stroke-width="1.6" stroke-linecap="round" stroke-linejoin="round">
        <path d="M7 12V5a2 2 0 0 1 4 0v9M11 12a2 2 0 0 1 4 0v2M15 13a2 2 0 0 1 4 0v6c0 5-3 9-8 9s-8-3-9-7l-1-4a2 2 0 0 1 3-2l3 3V12"/>
        <path d="M9 0v2M3 3l1.5 1.5M15 3l-1.5 1.5"/>
      </svg>
      Click Away
    </div>

    <div class="course-name">
      <span class="accent">Desktop &amp;</span><br>
      <span class="accent">Network Support</span><br>
      Course
    </div>

    <div class="tagline">Master Nimbus <span class="accent">Operating Systems</span></div>

    <div class="stat-pill one">
      <div class="stat-badge">
        <span class="big">90%</span>
        <span class="small">Employment Rate</span>
      </div>
      <span class="stat-label">CLASS OF 2024</span>
    </div>
    <div class="stat-pill two">
      <div class="stat-badge">
        <span class="lead">Prepare for</span>
        <span class="mid">3 OF THE</span>
      </div>
      <span class="stat-label">TOP 10 TECH JOBS</span>
    </div>

    <div class="source">NATIONAL CAREER REVIEW <span class="accent">2025</span></div>

    <ul class="checklist">
      <li><svg width="20" height="20" viewBox="0 0 20 20" fill="none" stroke="var(--lime)" stroke-width="1.8" stroke-linecap="round" stroke-linejoin="round"><path d="M16 10v6H3V4h9"/><path d="M7 9l3 3 8-9"/></svg>Hands-On Desktop &amp; Network Training</li>
      <li><svg width="20" height="20" viewBox="0 0 20 20" fill="none" stroke="var(--lime)" stroke-width="1.8" stroke-linecap="round" stroke-linejoin="round"><path d="M16 10v6H3V4h9"/><path d="M7 9l3 3 8-9"/></svg>Real-World Troubleshooting Skills</li>
      <li><svg width="20" height="20" viewBox="0 0 20 20" fill="none" stroke="var(--lime)" stroke-width="1.8" stroke-linecap="round" stroke-linejoin="round"><path d="M16 10v6H3V4h9"/><path d="M7 9l3 3 8-9"/></svg>Ready for IT Jobs</li>
    </ul>

    <div class="option-pill one">IN-PERSON AND REMOTE OPTIONS</div>
    <div class="option-pill two">PARTIAL SCHOLARSHIPS OFFERED</div>
  </section>
  <footer class="footer"></footer>
</div>
</body>
</html>
```